Corvane Capital Business Cards

These are professional business cards that are for my family office.
Put fake emails and phone numbers as of now until I finalize those components. This family office controls my families investments, assets, and future. The cards should be professional.
..
.
.
.
I just uploaded another variation of a logo I would like to see as a business card to I am inbeteen which logo to use

Target Market(s)

business

Industry/Entity Type

business

Contact Information for Business Card

Professional, wealth related, finance related.

Requirements
Must have
• Logo

```html
<!DOCTYPE html>
<html lang="en">
<head>
<meta charset="utf-8">
<title>Corvane Capital Business Cards</title>
<link rel="stylesheet" href="https://fonts.googleapis.com/css2?family=Cinzel:wght@600&family=Poppins:wght@400&display=swap">
<style>
  :root {
    --backdrop: #8c8c8c;
    --card-white: #ffffff;
    --card-navy: #1c1f2c;
    --ink: #1f2230;
    --ink-soft: #2b2d36;
    --mark-blue: #33457c;
    --mark-text: #3a4670;
  }
  * { margin: 0; padding: 0; box-sizing: border-box; }
  html, body {
    width: 1093px; height: 1200px; overflow: hidden;
    background: var(--backdrop);
  }
  .canvas { position: relative; width: 1093px; height: 1200px; }
  .card {
    position: absolute; left: 265px; width: 576px; height: 350px;
    border-radius: 24px;
  }
  .card--front { top: 226px; background: var(--card-white); color: var(--ink); }
  .card--back { top: 621px; background: var(--card-navy); }

  .holder { position: absolute; left: 26px; top: 46px; }
  .holder__name {
    font-family: "Cinzel", serif; font-weight: 600; font-size: 24px;
    line-height: 1; letter-spacing: 0.3px;
  }
  .holder__title {
    font-family: "Poppins", sans-serif; font-size: 16px; line-height: 1;
    margin-top: 4px; color: var(--ink-soft);
  }
  .brand {
    position: absolute; right: 24px; top: 58px;
    font-family: "Cinzel", serif; font-weight: 600; font-size: 28px;
    line-height: 1; letter-spacing: 0.5px;
  }
  .contacts {
    position: absolute; left: 26px; top: 258px; list-style: none;
    font-family: "Poppins", sans-serif; font-size: 16.5px; color: var(--ink-soft);
  }
  .contacts li { display: flex; align-items: center; height: 21px; }
  .contacts svg { width: 15px; height: 15px; margin-right: 7px; fill: var(--ink); }
  .address {
    position: absolute; right: 24px; top: 279px; text-align: right;
    font-family: "Poppins", sans-serif; font-size: 16.5px; line-height: 21px;
    color: var(--ink-soft); font-style: normal;
  }

  .back-mark {
    position: absolute; left: 210px; top: 70px; width: 166px; height: 166px;
    border: 3px solid var(--mark-blue); border-radius: 50%;
  }
  .back-brand {
    position: absolute; left: 0; right: 0; top: 254px; text-align: center;
    font-family: "Cinzel", serif; font-weight: 600; font-size: 34px;
    line-height: 1; color: var(--mark-text); letter-spacing: 0.5px;
  }
</style>
</head>
<body>
<main class="canvas">
  <section class="card card--front">
    <div class="holder">
      <h1 class="holder__name">EVERETT LANG</h1>
      <p class="holder__title">Managing Director</p>
    </div>
    <p class="brand">Corvane Capital</p>

    <ul class="contacts">
      <li>
        <svg viewBox="0 0 24 24" aria-hidden="true"><path d="M6.6 10.8a15.1 15.1 0 0 0 6.6 6.6l2.2-2.2a1 1 0 0 1 1-.25 11.4 11.4 0 0 0 3.6.57 1 1 0 0 1 1 1V20a1 1 0 0 1-1 1A17 17 0 0 1 3 4a1 1 0 0 1 1-1h3.5a1 1 0 0 1 1 1c0 1.25.2 2.46.57 3.6a1 1 0 0 1-.25 1z"/></svg>
        044-555 010 246
      </li>
      <li>
        <svg viewBox="0 0 24 24" aria-hidden="true"><path d="M2 5h20v14H2z M3 6l9 7 9-7" stroke="#fff" stroke-width="1.4"/></svg>
        office@corvanecap.com
      </li>
      <li>
        <svg viewBox="0 0 24 24" aria-hidden="true"><circle cx="12" cy="12" r="10"/><path d="M2 12h20M12 2c3 3 3 17 0 20M12 2c-3 3-3 17 0 20M4 7h16M4 17h16" stroke="#fff" stroke-width="1.3" fill="none"/></svg>
        www.corvanecap.com
      </li>
    </ul>

    <address class="address">18, Harlow Crescent Road<br>60210, Northbridge</address>
  </section>

  <section class="card card--back">
    <div class="back-mark" aria-hidden="true"></div>
    <p class="back-brand">Corvane Capital</p>
  </section>
</main>
</body>
</html>
```